TECH PROJECT NEEDS NEW SKINS FOR RE-BRANDING

We are a technology project that has a product (crypto wallet) nearing release, have basic designs made so far however we need NEW SKINS/ branding/ design options for this wallet to change the look and feel -- it will be called and re-branded as "KVORIL" a futuristic/ space/ edgy product so need it to look like so.

YOU ARE ALLOWED TO CHANGE + EXPERIMENT WITH THE LAYOUT/ schema and UI as you see fit -- (we are open to new and creative ideas)

(see KVORIL logo attached --- PLEASE USE THIS LOGO/ VERSIONS OF THIS LOGO IN YOUR DESIGNS/SKIN SUBMISSIONS -- WE PROVIDED THE ai file so feel free to alter the logo a bit to experiment if you want -- we are open and flexible to new creative ideas)

(FOR A MOOD BOARD FOR GUIDANCE on feel/colors/mood-- SEE "SAMPLE INTERFACE 1 & 2" ATTACHED)

Target Market(s)

TECHNOLOGY/SPACE/ FUTURE

Number of Pages Required

2 page

Colors

Designer to choose colors to be used in the design.

Requirements
Must have
• MUST USE OUR KVORIL LOGO OR A SIMILAR ALTERATION OF IT

```html
<!DOCTYPE html>
<html lang="en">
<head>
<meta charset="utf-8">
<title>KVORIL Wallets</title>
<link href="https://fonts.googleapis.com/css2?family=Barlow:wght@400;500;600&family=Montserrat:wght@700&display=swap" rel="stylesheet">
<style>
:root{
  --bg-main:#0f1615;
  --bg-rail:#18201f;
  --bg-panel:#141c1b;
  --row-a:#131b1a;
  --row-b:#0f1615;
  --head:#141c1b;
  --line:#2c3735;
  --text:#ffffff;
  --accent:#5fc79a;
  --accent-soft:#8fd6b1;
  --orange:#e4502a;
  --pending:#e57a2f;
  --cancel:#d8362c;
}
*{box-sizing:border-box;margin:0;padding:0}
html,body{width:1200px;height:776px;overflow:hidden;background:var(--bg-main)}
body{font-family:'Barlow',sans-serif;color:var(--text);position:relative}
.abs{position:absolute}
svg{display:block}

/* rail */
.rail{left:0;top:0;width:94px;height:776px;background:var(--bg-rail)}
.brand{left:0;top:52px;width:94px;text-align:center;font-weight:600;font-size:18px;letter-spacing:2px}
.nav-item{left:0;width:94px;text-align:center;font-size:10px;color:var(--accent-soft)}
.nav-item svg{margin:0 auto 5px}
.nav-item.active{background:linear-gradient(90deg,#1e2a28,#2f4440);border-right:2px solid var(--accent);color:#fff;height:65px;padding-top:16px}

/* wallet panel */
.panel{left:94px;top:0;width:230px;height:776px;background:var(--bg-panel)}
.panel-title{left:130px;top:31px;font-family:'Montserrat',sans-serif;font-weight:700;font-size:20px;letter-spacing:.5px}
.panel-sub{left:132px;top:60px;font-size:11px;color:var(--accent-soft)}
.search{border:1px solid var(--line);display:flex;align-items:center;justify-content:space-between;padding:0 13px;font-size:12.5px}
.wallet-search{left:132px;top:101px;width:181px;height:33px}
.wallet{left:132px;width:193px;height:40px;display:flex;align-items:center;font-size:11.5px;font-weight:600}
.wallet .dot{width:28px;height:28px;border-radius:50%;margin-right:10px;flex:none}
.wallet.active{background:linear-gradient(90deg,#1c2a27,#2e4540);border-right:2px solid var(--accent)}

/* header */
.coin-mark{left:366px;top:39px;width:54px;height:54px;border-radius:50%;background:var(--accent)}
.coin-title{left:440px;top:52px;font-size:24px;font-weight:500}
.label{font-size:10.5px;color:var(--accent-soft)}
.balance{left:362px;top:127px;font-size:35px;font-weight:400;letter-spacing:-.5px}
.usd{left:363px;top:176px;font-size:15px}
.address{left:363px;top:232px;font-size:12.5px}
.tab{left:888px;top:50px;width:176px;height:35px;border-left:2px solid var(--accent);background:linear-gradient(90deg,#2c3c39,rgba(44,60,57,0));font-size:11.5px;font-weight:600;padding:11px 0 0 15px}
.btn{top:131px;height:33px;background:var(--orange);display:flex;align-items:center;justify-content:center;gap:6px;font-size:11.5px;font-weight:500;color:#fff}
.btn-send{left:890px;width:128px}
.btn-receive{left:1028px;width:141px}
.tx-search{left:890px;top:209px;width:279px;height:33px}

/* table */
.table{left:364px;top:280px;width:805px}
.row{position:relative;height:50px;font-size:11px}
.row.head{height:49px;background:var(--head);color:var(--accent-soft);font-size:10.5px}
.row:nth-child(even){background:var(--row-a)}
.row:nth-child(odd):not(.head){background:var(--row-b)}
.cell{position:absolute;top:0;height:100%;display:flex;align-items:center;white-space:nowrap}
.c-act{left:19px}.c-act svg{margin-right:6px}
.head .c-act{left:20px}
.c-date{left:153px}
.head .c-date{left:134px;width:88px;padding-left:19px;background:linear-gradient(180deg,rgba(47,68,64,.2),#2f4440);border-bottom:2px solid var(--accent)}
.c-tx{left:246px}
.c-amt{left:446px}
.c-status{left:530px;font-weight:500}
.c-bal{left:617px}
.c-det{left:729px}
.details{border:1px solid var(--accent);color:var(--accent-soft);font-size:10px;width:57px;height:22px;display:flex;align-items:center;justify-content:center;letter-spacing:.3px}
.ok{color:var(--accent)}.pending{color:var(--pending)}.cancel{color:var(--cancel)}
</style>
</head>
<body>

<div class="abs rail"></div>
<div class="abs brand">KVORIL</div>

<div class="abs nav-item" style="top:122px">
  <svg width="16" height="16" viewBox="0 0 16 16" fill="none" stroke="#8fd6b1" stroke-width="1"><rect x="1" y="1" width="6" height="8"/><rect x="9" y="1" width="6" height="5"/><rect x="1" y="11" width="6" height="4"/><rect x="9" y="8" width="6" height="7"/></svg>Dashboard</div>
<div class="abs nav-item active" style="top:172px">
  <svg width="18" height="16" viewBox="0 0 18 16" fill="none" stroke="#fff" stroke-width="1"><rect x="1" y="4" width="16" height="11" rx="1"/><path d="M6 4V1h6v3M1 9h16M8 8h2v3H8z"/></svg>Portfolio</div>
<div class="abs nav-item" style="top:257px">
  <svg width="18" height="16" viewBox="0 0 18 16" fill="none" stroke="#8fd6b1" stroke-width="1"><rect x="1" y="4" width="16" height="11"/><path d="M3 4l9-3v3M12 8h5v3h-5z"/></svg>Wallete</div>
<div class="abs nav-item" style="top:324px">
  <svg width="12" height="18" viewBox="0 0 12 18" fill="none" stroke="#8fd6b1" stroke-width="1"><path d="M8 1L2 10h4l-2 7 6-9H6z"/></svg>Lighting</div>
<div class="abs nav-item" style="top:394px">
  <svg width="22" height="15" viewBox="0 0 22 15" fill="none" stroke="#8fd6b1" stroke-width="1"><path d="M5 14a4 4 0 010-8 6 6 0 0111-1 4.5 4.5 0 011 9z"/></svg>SKV Cloud</div>
<div class="abs nav-item" style="top:691px">
  <svg width="17" height="17" viewBox="0 0 24 24" fill="none" stroke="#8fd6b1" stroke-width="1.4"><circle cx="12" cy="12" r="3.2"/><path d="M12 2l2 3 3.5-.8.8 3.5 3 2-1.8 3 1.8 3-3 2-.8 3.5-3.5-.8-2 3-2-3-3.5.8-.8-3.5-3-2 1.8-3-1.8-3 3-2 .8-3.5 3.5.8z"/></svg>Settings</div>

<div class="abs panel"></div>
<div class="abs panel-title">WALLETS</div>
<div class="abs panel-sub">6 Active Wallets</div>
<div class="abs search wallet-search"><span>Search</span>
  <svg width="12" height="12" viewBox="0 0 12 12" fill="none" stroke="#fff" stroke-width="1.6"><circle cx="5" cy="5" r="3.8"/><path d="M8 8l3 3"/></svg></div>

<div class="abs wallet" style="top:176px"><span class="dot" style="background:#e8622a"></span>Quorvin - QVN</div>
<div class="abs wallet" style="top:226px"><span class="dot" style="background:#c8302a"></span>Dravix - DVX</div>
<div class="abs wallet" style="top:276px"><span class="dot" style="background:#3b4a48"></span>Ethvale - EVL</div>
<div class="abs wallet" style="top:326px"><span class="dot" style="background:#8fd6b1"></span>Lumora Coin - LMR</div>
<div class="abs wallet" style="top:376px"><span class="dot" style="background:#6c8480"></span>Tidelyn - TDL</div>
<div class="abs wallet active" style="top:422px;height:49px"><span class="dot" style="background:var(--accent)"></span>Stakvyn - SKV</div>

<div class="abs coin-mark"></div>
<div class="abs coin-title">Stakvyn - SKV</div>
<div class="abs label" style="left:364px;top:107px">Balance</div>
<div class="abs balance">320,167.92 SKV</div>
<div class="abs usd">= $ 32,016.79 USD</div>
<div class="abs label" style="left:364px;top:207px">Wallet Address</div>
<div class="abs address">XYZ1234000728399947622KLNJP096LK312</div>

<div class="abs tab">Stakvyn - SKV</div>
<div class="abs btn btn-send">
  <svg width="20" height="20" viewBox="0 0 20 20" fill="none" stroke="#fff" stroke-width="1.5"><circle cx="10" cy="10" r="8.5"/><path d="M10 15V6M6.5 9.5L10 6l3.5 3.5"/></svg>SEND MONEY</div>
<div class="abs btn btn-receive">
  <svg width="20" height="20" viewBox="0 0 20 20" fill="none" stroke="#fff" stroke-width="1.5"><circle cx="10" cy="10" r="8.5"/><path d="M10 5v9M6.5 10.5L10 14l3.5-3.5"/></svg>RECEIVE MONEY</div>
<div class="abs search tx-search"><span>Search Transactions</span>
  <svg width="12" height="12" viewBox="0 0 12 12" fill="none" stroke="#fff" stroke-width="1.6"><circle cx="5" cy="5" r="3.8"/><path d="M8 8l3 3"/></svg></div>

<div class="abs table">
  <div class="row head">
    <div class="cell c-act">ACTIVITY</div><div class="cell c-date">DATE</div><div class="cell c-tx">TRANSACTION ID</div>
    <div class="cell c-amt">AMOUNT</div><div class="cell c-status" style="font-weight:400">STATUS</div><div class="cell c-bal">BALANCE CHANGE</div><div class="cell c-det">DETAILS</div>
  </div>
  <div class="row"><div class="cell c-act"><svg width="15" height="15" viewBox="0 0 16 16" fill="none" stroke="#9aa8a5" stroke-width="1.2"><circle cx="8" cy="8" r="7"/><path d="M8 12V5M5.5 7.5L8 5l2.5 2.5"/></svg>Sending Money</div><div class="cell c-date">15 Nov 2018</div><div class="cell c-tx">XYZ123400123AY25DEFPLK0098AX</div><div class="cell c-amt">1.100 SKV</div><div class="cell c-status pending">PENDING</div><div class="cell c-bal">-320.167,92 SKV</div><div class="cell c-det"><span class="details">DETAILS</span></div></div>
  <div class="row"><div class="cell c-act"><svg width="15" height="15" viewBox="0 0 16 16" fill="none" stroke="#5fc79a" stroke-width="1.2"><circle cx="8" cy="8" r="7"/><path d="M8 4v7M5.5 8.5L8 11l2.5-2.5"/></svg>Money Received</div><div class="cell c-date">15 Nov 2018</div><div class="cell c-tx">XYZ123400123AY25DEFPLK0098AX</div><div class="cell c-amt">1.100 SKV</div><div class="cell c-status ok">SUCCESS</div><div class="cell c-bal">+320.167,92 SKV</div><div class="cell c-det"><span class="details">DETAILS</span></div></div>
  <div class="row"><div class="cell c-act"><svg width="15" height="15" viewBox="0 0 16 16" fill="none" stroke="#9aa8a5" stroke-width="1.2"><circle cx="8" cy="8" r="7"/><path d="M8 12V5M5.5 7.5L8 5l2.5 2.5"/></svg>Sending Money</div><div class="cell c-date">15 Nov 2018</div><div class="cell c-tx">XYZ123400123AY25DEFPLK0098AX</div><div class="cell c-amt">1.100 SKV</div><div class="cell c-status cancel">CANCELED</div><div class="cell c-bal">-320.167,92 SKV</div><div class="cell c-det"><span class="details">DETAILS</span></div></div>
  <div class="row"><div class="cell c-act"><svg width="15" height="15" viewBox="0 0 16 16" fill="none" stroke="#5fc79a" stroke-width="1.2"><circle cx="8" cy="8" r="7"/><path d="M8 4v7M5.5 8.5L8 11l2.5-2.5"/></svg>Money Received</div><div class="cell c-date">15 Nov 2018</div><div class="cell c-tx">XYZ123400123AY25DEFPLK0098AX</div><div class="cell c-amt">1.100 SKV</div><div class="cell c-status ok">SUCCESS</div><div class="cell c-bal">+320.167,92 SKV</div><div class="cell c-det"><span class="details">DETAILS</span></div></div>
  <div class="row"><div class="cell c-act"><svg width="15" height="15" viewBox="0 0 16 16" fill="none" stroke="#9aa8a5" stroke-width="1.2"><circle cx="8" cy="8" r="7"/><path d="M8 12V5M5.5 7.5L8 5l2.5 2.5"/></svg>Sending Money</div><div class="cell c-date">15 Nov 2018</div><div class="cell c-tx">XYZ123400123AY25DEFPLK0098AX</div><div class="cell c-amt">1.100 SKV</div><div class="cell c-status ok">SUCCESS</div><div class="cell c-bal">-320.167,92 SKV</div><div class="cell c-det"><span class="details">DETAILS</span></div></div>
  <div class="row"><div class="cell c-act"><svg width="15" height="15" viewBox="0 0 16 16" fill="none" stroke="#5fc79a" stroke-width="1.2"><circle cx="8" cy="8" r="7"/><path d="M8 4v7M5.5 8.5L8 11l2.5-2.5"/></svg>Sending Money</div><div class="cell c-date">15 Nov 2018</div><div class="cell c-tx">XYZ123400123AY25DEFPLK0098AX</div><div class="cell c-amt">1.100 SKV</div><div class="cell c-status ok">SUCCESS</div><div class="cell c-bal">+320.167,92 SKV</div><div class="cell c-det"><span class="details">DETAILS</span></div></div>
  <div class="row"><div class="cell c-act"><svg width="15" height="15" viewBox="0 0 16 16" fill="none" stroke="#9aa8a5" stroke-width="1.2"><circle cx="8" cy="8" r="7"/><path d="M8 12V5M5.5 7.5L8 5l2.5 2.5"/></svg>Sending Money</div><div class="cell c-date">15 Nov 2018</div><div class="cell c-tx">XYZ123400123AY25DEFPLK0098AX</div><div class="cell c-amt">1.100 SKV</div><div class="cell c-status cancel">CANCELED</div><div class="cell c-bal">-320.167,92 SKV</div><div class="cell c-det"><span class="details">DETAILS</span></div></div>
  <div class="row"><div class="cell c-act"><svg width="15" height="15" viewBox="0 0 16 16" fill="none" stroke="#5fc79a" stroke-width="1.2"><circle cx="8" cy="8" r="7"/><path d="M8 4v7M5.5 8.5L8 11l2.5-2.5"/></svg>Sending Money</div><div class="cell c-date">15 Nov 2018</div><div class="cell c-tx">XYZ123400123AY25DEFPLK0098AX</div><div class="cell c-amt">1.100 SKV</div><div class="cell c-status ok">SUCCESS</div><div class="cell c-bal">+320.167,92 SKV</div><div class="cell c-det"><span class="details">DETAILS</span></div></div>
</div>

</body>
</html>
```